Tech Savy small Business accountant business card design

We need a business card for a new company based in the cloud. We provide tax, business advisory, accounting, information technology solutions and back office functions to small businesses. We offer fixed fee packages with add on services as you need them. By harnessing technology we simplify small business operational processes providing valuable time and information for small business owners to grow their business. In the logo (bluvoria) we want to be able to see bluv and experts. The final design should communicate achieving growth dreams and balance (ie life and $).
Updates
This project has been temporarily placed on hold until I finalize "Tech Savy small Business accountant needs a logo". I invite all designers to submit on this logo project. Once my logo is finalized I will resume this business card contest. Thanks Added Wednesday, March 19, 2014
This project has been temporarily placed on hold until I finalize "Tech Savy small Business accountant logo". I invite all designers to submit on this logo project. Once my logo is finalized I will resume this business card contest. Thanks Added Thursday, March 20, 2014
Target Market(s)
Small Business (Revenue $500,000, more than 3 employees) owners.
Industry/Entity Type
Small Business
Contact Information for Business Card
Marcy Elwind (Principal)
Accountant, Tax Agent.
TEL | 0417 683 912
EMAIL | Marcy.Elwind@bluvoria.com.au
WEB | www.bluvoria.com.au
Look and feel

```html
<!DOCTYPE html>
<html lang="en">
<head>
<meta charset="utf-8">
<title>bluvoria business card</title>
<link rel="stylesheet" href="https://fonts.googleapis.com/css2?family=Source+Sans+3:wght@400;600;700&display=swap">
<style>
  :root {
    --blue: #1e96d4;
    --blue-deep: #1a86c2;
    --grey: #6d6e71;
    --grey-text: #58595b;
    --web-text: #5a4a44;
    --white: #ffffff;
    --backdrop: #e9e7e4;
  }
  * { margin: 0; padding: 0; box-sizing: border-box; }
  html, body {
    width: 1200px; height: 1000px; overflow: hidden;
    background: var(--backdrop);
    font-family: "Source Sans 3", "Myriad Pro", Arial, sans-serif;
  }
  .card {
    position: absolute; left: 266px; width: 664px; height: 396px;
    border-radius: 22px; overflow: hidden;
    box-shadow: 0 6px 16px rgba(0,0,0,0.18);
  }
  .card-front { top: 74px; background: var(--white); }
  .card-back { top: 532px; background: var(--blue); }
  .card > svg { position: absolute; inset: 0; display: block; }

  .brand { position: absolute; left: 38px; top: 148px; }
  .brand-name {
    font-size: 62px; font-weight: 600; color: var(--blue);
    letter-spacing: -0.5px; line-height: 1;
  }
  .brand-tagline {
    margin-top: 10px; font-size: 17.5px; color: var(--grey-text);
  }

  .holder { position: absolute; right: 38px; top: 94px; text-align: right; color: var(--white); }
  .holder-name { font-size: 25px; font-weight: 700; line-height: 1.1; }
  .holder-role { font-size: 17px; font-weight: 400; }
  .holder-title { font-size: 17.5px; line-height: 1.35; }

  .contacts { position: absolute; right: 38px; top: 246px; list-style: none; color: var(--white); font-size: 17px; }
  .contacts li { display: flex; justify-content: flex-end; align-items: center; gap: 9px; height: 25px; }
  .contacts svg { width: 15px; height: 15px; }

  .back-field {
    position: absolute; left: 0; top: 0; width: 400px; height: 396px;
    background: linear-gradient(100deg, var(--grey) 0%, var(--blue-deep) 45%, var(--blue) 100%);
  }
  .back-text { position: absolute; left: 308px; top: 174px; }
  .back-tagline { font-size: 19.5px; color: var(--white); }
  .back-web { margin-top: 4px; margin-left: 36px; font-size: 14px; letter-spacing: 4.6px; color: var(--web-text); }
</style>
</head>
<body>

<section class="card card-front">
  <svg width="664" height="396" viewBox="0 0 664 396" aria-hidden="true">
    <polygon points="272,0 664,0 664,396 272,396 410,198" fill="var(--blue)"/>
    <polygon points="252,0 264,0 402,198 264,396 252,396 390,198" fill="var(--grey)"/>
  </svg>

  <div class="brand">
    <div class="brand-name">bluvoria</div>
    <div class="brand-tagline">Your business and accounting partner</div>
  </div>

  <div class="holder">
    <div class="holder-name">Marcy Elwind <span class="holder-role">/ Principal</span></div>
    <div class="holder-title">Accountant, Tax Agent</div>
  </div>

  <ul class="contacts">
    <li>0417 683 912
      <svg viewBox="0 0 16 16" aria-hidden="true"><path d="M2 6c0-2 3-3 6-3s6 1 6 3v1h-3V6H5v1H2z M4 8h8l1 5H3z" fill="var(--white)"/></svg>
    </li>
    <li>Marcy.Elwind@bluvoria.com.au
      <svg viewBox="0 0 16 16" aria-hidden="true"><rect x="1.5" y="3.5" width="13" height="9" fill="none" stroke="var(--white)" stroke-width="1.4"/><path d="M1.5 3.5 8 9l6.5-5.5" fill="none" stroke="var(--white)" stroke-width="1.4"/></svg>
    </li>
    <li>www.bluvoria.com.au
      <svg viewBox="0 0 16 16" aria-hidden="true"><g fill="none" stroke="var(--white)" stroke-width="1.2"><circle cx="8" cy="8" r="6.3"/><ellipse cx="8" cy="8" rx="2.8" ry="6.3"/><path d="M1.7 8h12.6M3 4.5h10M3 11.5h10"/></g></svg>
    </li>
  </ul>
</section>

<section class="card card-back">
  <div class="back-field" role="img" aria-label="Decorative brand graphic area in grey, blue and white"></div>

  <div class="back-text">
    <div class="back-tagline">Your Business and Accounting Parthner</div>
    <div class="back-web">www.bluvoria.com.au</div>
  </div>
</section>

</body>
</html>
```